Website Design for Architecture Practice

I need a home page and one sidebar/content page for an Architecture practice delivered in PSD.

This archictecture practice specialises in one-off, high end homes and commercial properties (restaurant) heavily influenced by Edmund Harcourt Vale, particularly his work on the Pellworth Museum

I am looking for a home page, and a generic content page where we can outline our services, and showcase our homes.

http://journals.kestrelhill.edu.au/artnotes/Pellworth%20Quayside%202.jpg

Target Market(s)

30-70yr old (typically wealthy) property buyers, developers and investors

Industry/Entity Type

Architecture

Number of Pages Required

2 page

Font styles to use
Serif
Sans Serif

Requirements
Must have
• Home page design
• a Content Page design (ie, top nav with sidebar)
Nice to have
• Use any Edmund Harcourt Vale images you can find via google etc as placeholders for our own photography (ie they don't need to be licensed as we will be replacing with our own commissioned photography). Full color preferred but feel free to experiment with treating any images as you see fit.

```html
<!DOCTYPE html>
<html lang="en">
<head>
<meta charset="utf-8">
<title>Crestmoor Architect — Home</title>
<link href="https://fonts.googleapis.com/css2?family=Open+Sans:wght@400;600;700&family=Playfair+Display:ital,wght@1,700&display=swap" rel="stylesheet">
<style>
:root{
  --green:#8cc63f;
  --green-dark:#6fa52a;
  --orange:#f7941d;
  --ink:#2b2b2b;
  --text:#666;
  --muted:#999;
  --topbar:#2a2a2a;
  --footer:#333333;
  --footer-deep:#262626;
  --paper:#ffffff;
  --soft:#f4f4f4;
}
*{box-sizing:border-box;margin:0;padding:0}
html,body{width:750px;height:1200px;overflow:hidden;background:var(--paper)}
body{font-family:"Open Sans",Arial,sans-serif;color:var(--text);font-size:10px;position:relative}

.topbar{height:20px;background:var(--topbar);display:flex;align-items:center;justify-content:space-between;padding:0 88px;color:#ccc;font-size:8px}
.topbar .phone{display:flex;align-items:center;gap:5px}
.social{display:flex;gap:6px}
.social span{width:12px;height:12px;border-radius:50%;background:#555;display:block}

.header{height:62px;display:flex;align-items:center;justify-content:space-between;padding:0 88px}
.brand{display:flex;align-items:center;gap:6px}
.brand .mark{width:22px;height:22px;background:var(--green)}
.brand .name{font-weight:700;font-size:17px;color:var(--ink);letter-spacing:.5px}
.nav{display:flex;align-items:center;gap:4px}
.nav a{font-size:9px;font-weight:600;color:var(--ink);text-decoration:none;padding:8px 14px}
.nav a.active{background:var(--green);color:#fff}
.nav .search{width:18px;height:18px;border-radius:50%;border:1px solid var(--green);margin-left:8px;display:flex;align-items:center;justify-content:center}

.hero{height:293px;position:relative;background:linear-gradient(180deg,#b9c7cf 0%,#d9dcd6 30%,#7b5a44 48%,#5c4434 62%,#5d7a3b 80%,#3e5a28 100%);display:flex;flex-direction:column;align-items:center;justify-content:center;text-align:center}
.hero .headline{font-family:"Playfair Display",Georgia,serif;font-style:italic;font-weight:700;font-size:26px;line-height:1.35;color:#fff;text-shadow:0 1px 3px rgba(0,0,0,.5)}
.hero .headline .accent{color:var(--orange)}
.hero .arrow{position:absolute;top:50%;width:22px;height:22px;margin-top:-11px;background:rgba(255,255,255,.85);border-radius:50%;display:flex;align-items:center;justify-content:center}
.hero .arrow.prev{left:-4px}
.hero .arrow.next{right:-4px}

.section-title{text-align:center;font-size:19px;font-weight:700;color:var(--ink)}
.section-title .hl{color:var(--green)}

.about{height:175px;padding:28px 88px 0;text-align:center}
.about .section-title{display:flex;align-items:center;justify-content:center;gap:8px}
.about .section-title .hl{color:var(--orange)}
.about .brand .name{font-size:15px}
.about p{margin-top:14px;font-size:8px;line-height:1.7;color:var(--muted)}

.projects{height:200px;padding-top:20px;background:var(--soft)}
.project-grid{display:flex;justify-content:center;gap:22px;margin-top:16px}
.project{width:170px;height:95px;border:4px solid var(--green);position:relative}
.project .photo{position:absolute;inset:0}
.project .caption{position:absolute;left:-4px;bottom:12px;background:var(--orange);color:#fff;font-size:8px;padding:4px 8px}
.p1 .photo{background:linear-gradient(180deg,#9fc3e0,#7a8f6a 60%,#4b6b2f)}
.p2 .photo{background:linear-gradient(180deg,#8fb7da,#6b5646 55%,#5b7a3a)}
.p3 .photo{background:linear-gradient(180deg,#c7dbe9,#b89a78 55%,#8a7458)}

.testimonials{height:160px;padding-top:18px}
.testimonial-row{display:flex;justify-content:center;gap:40px;margin-top:16px}
.testimonial{width:270px;display:flex;gap:12px;align-items:flex-start}
.avatar{width:52px;height:52px;border-radius:50%;background:radial-gradient(circle,#c9a58a,#7a5a48);border:3px solid #eee;flex:none}
.quote-box{flex:1}
.quote{border:1px solid #e2e2e2;padding:8px 10px;font-size:8px;line-height:1.6;color:var(--muted);font-style:italic;box-shadow:0 2px 3px rgba(0,0,0,.06)}
.author{margin-top:8px;font-size:8px;color:var(--ink);text-align:center}

.newsletter{height:72px;display:flex;align-items:center;justify-content:center;gap:14px;background:var(--soft);border-top:1px solid #e6e6e6}
.newsletter .icon{width:34px;height:34px;border-radius:50%;background:var(--green);display:flex;align-items:center;justify-content:center}
.newsletter .label{font-size:10px;font-weight:600;color:var(--ink);line-height:1.4;width:200px}
.newsletter .label .hl{color:var(--orange);font-weight:700}
.newsletter .field{width:245px;height:26px;border:1px solid #ddd;background:#fff;font-size:8px;color:var(--muted);padding:8px 8px}
.newsletter .btn{height:26px;padding:0 14px;background:var(--ink);color:#fff;font-size:8px;font-weight:700;display:flex;align-items:center}

.footer{height:196px;background:var(--footer);display:flex;padding:18px 88px 0;gap:30px;color:#bbb}
.footer .col{flex:1}
.footer h4{font-size:10px;font-weight:700;color:#fff;display:flex;align-items:center;gap:8px;padding-bottom:8px;border-bottom:1px solid #484848;margin-bottom:8px}
.footer h4 .dot{width:14px;height:14px;border-radius:50%;background:var(--green);display:flex;align-items:center;justify-content:center}
.links li{list-style:none;font-size:8px;line-height:2;display:flex;align-items:center;gap:5px}
.links li::before{content:"";width:3px;height:3px;background:var(--green)}
.address{font-size:8px;line-height:1.6}
.address strong{color:#fff;font-weight:600}
.contact-line{display:flex;align-items:center;gap:6px;margin-top:6px;font-size:8px}
.contact-line.big{font-size:13px;color:#fff;font-weight:700}
.footer .social{margin-top:8px}
.footer .social span{background:#555;width:14px;height:14px}
.form-row{display:flex;align-items:center;gap:6px;margin-bottom:5px;font-size:8px}
.form-row .lbl{width:36px}
.form-row .box{flex:1;height:14px;background:#fff}
.form-row.msg .box{height:34px}
.send{float:right;background:var(--green);color:#fff;font-size:8px;font-weight:700;padding:4px 10px}
.copyright{height:23px;background:var(--footer-deep);color:#888;font-size:8px;display:flex;align-items:center;justify-content:center}
</style>
</head>
<body>

<div class="topbar">
  <div class="phone">
    <svg width="8" height="8" viewBox="0 0 10 10"><path d="M2 1l2 2-1 1.2c.6 1.2 1.6 2.2 2.8 2.8L7 6l2 2-1.3 1.3C4.5 9 1 5.5.7 2.3z" fill="#8cc63f"/></svg>
    (0198) 552-0417
  </div>
  <div class="social"><span></span><span></span><span></span><span></span></div>
</div>

<header class="header">
  <div class="brand"><span class="mark"></span><span class="name">CRESTMOOR</span></div>
  <nav class="nav">
    <a class="active">Home</a><a>About Us</a><a>Projects</a><a>Clients</a><a>Contact Us</a>
    <span class="search"><svg width="8" height="8" viewBox="0 0 10 10"><circle cx="4" cy="4" r="3" fill="none" stroke="#8cc63f" stroke-width="1.4"/><path d="M6.3 6.3L9 9" stroke="#8cc63f" stroke-width="1.4"/></svg></span>
  </nav>
</header>

<section class="hero" role="img" aria-label="Photograph of a low brick prairie-style house with wide eaves, lawn and trees">
  <p class="headline">We Are Specialises In One-off<br><span class="accent">High End Homes And Commercial Properties</span></p>
  <span class="arrow prev"><svg width="8" height="8" viewBox="0 0 10 10"><path d="M7 1L3 5l4 4" fill="none" stroke="#333" stroke-width="1.6"/></svg></span>
  <span class="arrow next"><svg width="8" height="8" viewBox="0 0 10 10"><path d="M3 1l4 4-4 4" fill="none" stroke="#333" stroke-width="1.6"/></svg></span>
</section>

<section class="about">
  <h2 class="section-title"><span class="hl">About</span><span class="brand"><span class="name">CRESTMOOR</span></span></h2>
  <p>Our studio shapes one-off homes and commercial spaces with a quiet respect for landscape, craft and proportion. Every project begins with listening, then grows through careful sketches, honest materials and close work with builders. We draw on the long horizontal lines of prairie houses to create rooms that feel calm, warm and open to light.</p>
</section>

<section class="projects">
  <h2 class="section-title"><span class="hl">Recent</span> Project</h2>
  <div class="project-grid">
    <div class="project p1"><div class="photo" role="img" aria-label="Photograph of a timber house among trees"></div><span class="caption">Lorem ipsum dolor sit amet</span></div>
    <div class="project p2"><div class="photo" role="img" aria-label="Photograph of a steep-roofed brick home"></div><span class="caption">Lorem ipsum dolor sit amet</span></div>
    <div class="project p3"><div class="photo" role="img" aria-label="Photograph of a curved museum building"></div><span class="caption">Lorem ipsum dolor sit amet</span></div>
  </div>
</section>

<section class="testimonials">
  <h2 class="section-title"><span class="hl">Client</span> Testimonials</h2>
  <div class="testimonial-row">
    <div class="testimonial">
      <div class="avatar" role="img" aria-label="Client portrait photograph"></div>
      <div class="quote-box">
        <p class="quote">They listened closely and delivered a home that feels both bold and calm. Every detail was handled with care from first sketch to handover.</p>
        <p class="author">Iona Reeve</p>
      </div>
    </div>
    <div class="testimonial">
      <div class="avatar" role="img" aria-label="Client portrait photograph"></div>
      <div class="quote-box">
        <p class="quote">Our restaurant now draws guests for the building alone. The team balanced budget, light and materials with real patience and skill.</p>
        <p class="author">Corwin Ashdale</p>
      </div>
    </div>
  </div>
</section>

<section class="newsletter">
  <span class="icon"><svg width="16" height="12" viewBox="0 0 16 12"><rect x="1" y="1" width="14" height="10" fill="none" stroke="#fff" stroke-width="1.4"/><path d="M1 1l7 6 7-6" fill="none" stroke="#fff" stroke-width="1.4"/></svg></span>
  <p class="label">Subscribe To Our Newsletter For<br>The <span class="hl">MONTHLY SPECIALS</span></p>
  <div class="field">Enter Your Email Here</div>
  <div class="btn">SUBSCRIBE</div>
</section>

<footer class="footer">
  <div class="col">
    <h4><span class="dot"></span>QUICK LINKS</h4>
    <ul class="links"><li>Home</li><li>About</li><li>Service</li><li>Project</li><li>Clients</li><li>Contact Us</li></ul>
  </div>
  <div class="col">
    <h4><span class="dot"></span>CONTACT ADDRESS</h4>
    <p class="address"><strong>Crestmoor Architect</strong><br>24 Larkfield Lane, Harrow Point<br>Westbridge, NW 40218</p>
    <p class="contact-line big"><svg width="10" height="10" viewBox="0 0 10 10"><path d="M2 1l2 2-1 1.2c.6 1.2 1.6 2.2 2.8 2.8L7 6l2 2-1.3 1.3C4.5 9 1 5.5.7 2.3z" fill="#8cc63f"/></svg>0198-552-0417</p>
    <p class="contact-line"><svg width="10" height="8" viewBox="0 0 10 8"><rect x=".5" y=".5" width="9" height="7" fill="none" stroke="#8cc63f"/><path d="M.5.5L5 4.5 9.5.5" fill="none" stroke="#8cc63f"/></svg>hello@crestmoorstudio.com</p>
    <div class="social"><span></span><span></span><span></span><span></span></div>
  </div>
  <div class="col">
    <h4><span class="dot"></span>QUICK CONTACT</h4>
    <div class="form-row"><span class="lbl">Name</span><span class="box"></span></div>
    <div class="form-row"><span class="lbl">Email</span><span class="box"></span></div>
    <div class="form-row msg"><span class="lbl">Message</span><span class="box"></span></div>
    <span class="send">SUBMIT</span>
  </div>
</footer>
<div class="copyright">© 2024 Crestmoor Architect. All Rights Reserved.</div>

</body>
</html>
```